Bright Harbor Painters Banner

Create a banner that displays and reinforces Bright Harbor Painters’ brand identity while promoting our interior painting services. The banner will be displayed at indoor venues through the winter. The design should be clean, professional, and visually recognizable to both new and returning customers. See attached design brief & logo source files.

```html
<!DOCTYPE html>
<html lang="en">
<head>
<meta charset="UTF-8">
<title>Bright Harbor Painters – Interior Painting Banner</title>
<link href="https://fonts.googleapis.com/css2?family=Montserrat:wght@700;800&family=Open+Sans:wght@700&family=Poppins:wght@400;600;700;800&display=swap" rel="stylesheet">
<style>
  :root {
    --charcoal: #3f4041;
    --brand-green: #6aac44;
    --alert-red: #e3120b;
    --ink: #333435;
    --white: #ffffff;
    --backdrop: #e9e9e9;
    --photo-light: #e6d3b4;
    --photo-mid: #a27c55;
    --photo-dark: #4a3022;
  }
  * { margin: 0; padding: 0; box-sizing: border-box; }
  html, body {
    width: 1200px; height: 610px; overflow: hidden;
    background: var(--backdrop);
  }
  .stage { position: relative; width: 1200px; height: 610px; }
  .banner {
    position: absolute; left: 0; top: 64px;
    width: 1240px; height: 497px;
    transform: scale(0.9677); transform-origin: 0 0;
    overflow: hidden;
    background: var(--white);
  }
  .banner-shapes { position: absolute; inset: 0; }
  .headline-top {
    position: absolute; left: 33px; top: 40px;
    font: 800 57px/1 "Montserrat", sans-serif;
    color: var(--brand-green); letter-spacing: 1px;
  }
  .headline-main {
    position: absolute; left: 30px; top: 98px;
    font: 800 114px/1 "Montserrat", sans-serif;
    color: var(--white); letter-spacing: 1px;
  }
  .tagline {
    position: absolute; left: 35px; top: 212px;
    width: 683px; height: 50px;
    background: var(--alert-red);
    border-radius: 12px 12px 0 0;
    color: var(--white);
    font: 700 25px/50px "Open Sans", sans-serif;
    text-align: center; letter-spacing: 0.2px;
  }
  .services-label {
    position: absolute; left: 33px; top: 276px;
    font: 600 37px/1.02 "Poppins", sans-serif;
    color: var(--white);
  }
  .services-divider {
    position: absolute; left: 250px; top: 290px;
    width: 2px; height: 60px; background: var(--charcoal);
  }
  .services-list {
    position: absolute; left: 273px; top: 280px;
    list-style: none;
    display: grid; grid-template-columns: auto auto auto;
    column-gap: 10px; row-gap: 2px;
    font: 700 30px/37px "Poppins", sans-serif;
    color: var(--ink);
  }
  .services-list li { display: flex; align-items: center; gap: 4px; white-space: nowrap; }
  .services-list li.span-2 { grid-column: span 2; }
  .tick { width: 20px; height: 20px; flex: none; }
  .brand {
    position: absolute; left: 35px; top: 395px;
    display: flex; align-items: center; gap: 12px;
  }
  .brand-mark { width: 38px; height: 38px; background: var(--charcoal); }
  .brand-name {
    font: 800 27px/1.05 "Poppins", sans-serif;
    color: var(--brand-green); text-transform: uppercase;
  }
  .cta {
    position: absolute; left: 322px; top: 394px;
    font: 700 32px/1 "Poppins", sans-serif;
    color: var(--ink);
  }
  .cta .highlight { color: var(--alert-red); }
  .web {
    position: absolute; left: 324px; top: 437px;
    display: flex; align-items: center; gap: 12px;
    font: 400 34px/1 "Poppins", sans-serif;
    color: var(--ink);
  }
  .web .domain { color: var(--brand-green); }
  .globe { width: 28px; height: 28px; }
</style>
</head>
<body>
<main class="stage">
  <section class="banner">
    <svg class="banner-shapes" viewBox="0 0 1240 497" width="1240" height="497">
      <defs>
        <linearGradient id="interiorTones" x1="0" y1="0" x2="0" y2="1">
          <stop offset="0" stop-color="var(--photo-light)"/>
          <stop offset="0.55" stop-color="var(--photo-mid)"/>
          <stop offset="1" stop-color="var(--photo-dark)"/>
        </linearGradient>
      </defs>
      <rect class="header-panel" x="0" y="0" width="1240" height="262" fill="var(--charcoal)"/>
      <polygon class="services-band" points="855,0 1240,0 1240,375 0,375 0,262 709,262" fill="var(--brand-green)"/>
      <rect class="footer-panel" x="0" y="375" width="1240" height="122" fill="var(--white)"/>
      <polygon class="chevron-edge" points="870,0 1240,0 1240,497 870,497 725,247" fill="var(--white)"/>
      <polygon class="interior-photo" role="img" aria-label="Photo of a freshly painted living room with a cream beamed ceiling, pendant lights and a stone fireplace" points="880,0 1240,0 1240,497 880,497 736,247" fill="url(#interiorTones)"/>
    </svg>

    <h1 class="headline-top">INTERIOR PAINTING</h1>
    <h2 class="headline-main">SERVICES</h2>
    <p class="tagline">TRUSTED LOCAL PROFESSIONALS, SINCE 2005</p>

    <p class="services-label">OUR<br>SERVICES</p>
    <div class="services-divider"></div>
    <ul class="services-list">
      <li><svg class="tick" viewBox="0 0 20 20"><circle cx="10" cy="10" r="10" fill="#fff"/><path d="M5.5 10.5l3 3 6-6.5" stroke="var(--brand-green)" stroke-width="2.4" fill="none" stroke-linecap="round" stroke-linejoin="round"/></svg>Walls</li>
      <li><svg class="tick" viewBox="0 0 20 20"><circle cx="10" cy="10" r="10" fill="#fff"/><path d="M5.5 10.5l3 3 6-6.5" stroke="var(--brand-green)" stroke-width="2.4" fill="none" stroke-linecap="round" stroke-linejoin="round"/></svg>Ceilings</li>
      <li><svg class="tick" viewBox="0 0 20 20"><circle cx="10" cy="10" r="10" fill="#fff"/><path d="M5.5 10.5l3 3 6-6.5" stroke="var(--brand-green)" stroke-width="2.4" fill="none" stroke-linecap="round" stroke-linejoin="round"/></svg>Trim</li>
      <li><svg class="tick" viewBox="0 0 20 20"><circle cx="10" cy="10" r="10" fill="#fff"/><path d="M5.5 10.5l3 3 6-6.5" stroke="var(--brand-green)" stroke-width="2.4" fill="none" stroke-linecap="round" stroke-linejoin="round"/></svg>Cabinets</li>
      <li class="span-2"><svg class="tick" viewBox="0 0 20 20"><circle cx="10" cy="10" r="10" fill="#fff"/><path d="M5.5 10.5l3 3 6-6.5" stroke="var(--brand-green)" stroke-width="2.4" fill="none" stroke-linecap="round" stroke-linejoin="round"/></svg>Drywall Repair</li>
    </ul>

    <div class="brand">
      <span class="brand-mark"></span>
      <span class="brand-name">Bright Harbor<br>Painters</span>
    </div>

    <p class="cta">Book a <span class="highlight">Free Estimate</span> at</p>
    <p class="web">
      <svg class="globe" viewBox="0 0 28 28"><circle cx="14" cy="14" r="14" fill="var(--brand-green)"/><g stroke="#fff" stroke-width="1.6" fill="none"><circle cx="14" cy="14" r="8"/><ellipse cx="14" cy="14" rx="3.5" ry="8"/><line x1="6" y1="14" x2="22" y2="14"/></g></svg>
      <span>www.<span class="domain">bhpainters</span>.com</span>
    </p>
  </section>
</main>
</body>
</html>
```